equestrian poster

Could you make the poster an elete looking poster for a sports event using the building on the back ground and photo shop the horse there also please make an sporty luxery poster
the dates for next year are 27th till 31 st may and 16 till 19 plus 23rd till 26 juli

our colors are green and gray

Target Market(s)

tourist and public

Industry/Entity Type

equestrian event interna

Other font styles liked:
• caslon classico font

Colors
00AB8E
00BBA5
67D7C9
C6EFE9
E9F9F6

```html
<!DOCTYPE html>
<html lang="en">
<head>
<meta charset="utf-8">
<title>Stal Lindenhorst – Event Poster</title>
<link href="https://fonts.googleapis.com/css2?family=Exo+2:wght@500;600;700;800&family=Libre+Caslon+Text&display=swap" rel="stylesheet">
<style>
  :root{
    --bg:#8b8c8f;
    --paper:#ffffff;
    --green-deep:#08382a;
    --green:#0d5a45;
    --green-glow:#127a63;
    --teal:#74b7b5;
    --ink-green:#0f4d2f;
    --month:#4f8c78;
    --footer-gray:#7d807f;
    --footer-green:#0f4a2a;
    --divider:#c9cbca;
  }
  *{margin:0;padding:0;box-sizing:border-box}
  html,body{width:1200px;height:1200px;overflow:hidden;background:var(--bg)}
  body{font-family:"Exo 2",sans-serif}
  .poster{position:absolute;left:176px;top:0;width:848px;height:1200px;background:var(--paper);overflow:hidden}
  .band-art{position:absolute;inset:0;width:848px;height:1200px}
  .photo-venue{position:absolute;left:18px;top:40px;width:440px;height:520px;
    background:linear-gradient(180deg,#b59282 0%,#cdb5aa 45%,rgba(255,255,255,0) 100%)}
  .photo-jumper{position:absolute;left:420px;top:40px;width:410px;height:620px;z-index:3;border-radius:6px;
    background:linear-gradient(180deg,#5d617a 0%,#8a7463 45%,#a97e5c 100%)}
  .title{position:absolute;left:0;width:848px;top:744px;text-align:center;color:#fff;
    font-weight:700;font-size:72px;letter-spacing:1px;line-height:1;text-shadow:0 3px 8px rgba(0,0,0,.35);z-index:4}
  .since{position:absolute;left:0;width:848px;top:826px;text-align:center;color:#fff;font-weight:700;font-size:26px;z-index:4}
  .brand{position:absolute;left:0;width:848px;top:918px;display:flex;flex-direction:column;align-items:center;gap:10px}
  .brand-dot{width:76px;height:76px;border-radius:50%;background:var(--ink-green)}
  .brand-name{font-family:"Libre Caslon Text",serif;font-size:28px;line-height:1.1;color:var(--ink-green)}
  .dates{position:absolute;left:0;top:1064px;width:848px;height:66px}
  .date{position:absolute;width:240px;margin-left:-120px;text-align:center}
  .date:nth-child(1){left:174px}.date:nth-child(2){left:423px}.date:nth-child(3){left:673px}
  .date-days{font-weight:700;font-size:31px;color:var(--ink-green);line-height:1}
  .date-days sup{font-size:16px;vertical-align:top;position:relative;top:-1px}
  .date-month{font-weight:500;font-size:22px;color:var(--month);line-height:1.2;margin-top:3px}
  .divider{position:absolute;top:1064px;width:1px;height:66px;background:var(--divider)}
  .footer{position:absolute;left:0;top:1154px;width:848px;height:33px;display:flex;font-size:14px;color:#fff;font-weight:500}
  .footer-social{flex:0 0 548px;background:var(--footer-gray);display:flex;align-items:center;padding-left:32px;gap:10px}
  .social-dot{width:19px;height:19px;border-radius:50%;background:#fff}
  .footer-web{flex:1;background:var(--footer-green);display:flex;align-items:center;justify-content:center;gap:10px}
  .footer-web svg{width:20px;height:20px}
</style>
</head>
<body>
<main class="poster">
  <div class="photo-venue" role="img" aria-label="Photo of the clubhouse of the equestrian centre, fading into white"></div>

  <svg class="band-art" viewBox="0 0 848 1200" aria-hidden="true">
    <defs>
      <linearGradient id="swoosh-gray" x1="0" y1="0" x2="1" y2="0">
        <stop offset="0" stop-color="#c9cacc"/><stop offset=".6" stop-color="#f2f2f3" stop-opacity=".4"/><stop offset="1" stop-color="#fff" stop-opacity="0"/>
      </linearGradient>
      <linearGradient id="swoosh-teal" x1="1" y1="0" x2="0" y2="0">
        <stop offset="0" stop-color="#5f9e92"/><stop offset="1" stop-color="#5f9e92" stop-opacity="0"/>
      </linearGradient>
      <radialGradient id="band-fill" cx=".5" cy=".55" r=".6">
        <stop offset="0" stop-color="#127a63"/><stop offset=".6" stop-color="#0d5a45"/><stop offset="1" stop-color="#08382a"/>
      </radialGradient>
    </defs>
    <path d="M0,470 Q260,640 620,650 L620,720 Q300,700 0,590 Z" fill="url(#swoosh-gray)"/>
    <path d="M848,327 Q650,370 590,640 L848,640 Z" fill="url(#swoosh-teal)"/>
    <path d="M0,598 Q424,792 848,603" fill="none" stroke="#74b7b5" stroke-width="18"/>
    <path d="M0,1002 Q424,736 848,1033" fill="none" stroke="#74b7b5" stroke-width="22"/>
    <path d="M0,614 Q424,808 848,619 L848,1017 Q424,752 0,986 Z" fill="url(#band-fill)"/>
  </svg>

  <div class="photo-jumper" role="img" aria-label="Cut-out photo of a show jumper on a bay horse clearing a fence"></div>

  <h1 class="title">STAL LINDENHORST</h1>
  <p class="since">SINCE 2005</p>

  <div class="brand">
    <span class="brand-dot"></span>
    <span class="brand-name">Stal Lindenhorst</span>
  </div>

  <section class="dates">
    <div class="date"><div class="date-days">27<sup>TH</sup> - 31<sup>ST</sup></div><div class="date-month">MAY 2026</div></div>
    <div class="date"><div class="date-days">16<sup>TH</sup> - 19<sup>TH</sup></div><div class="date-month">JULI 2026</div></div>
    <div class="date"><div class="date-days">23<sup>RD</sup> - 26<sup>TH</sup></div><div class="date-month">JULI 2026</div></div>
  </section>
  <span class="divider" style="left:298px"></span>
  <span class="divider" style="left:548px"></span>

  <footer class="footer">
    <div class="footer-social"><span class="social-dot"></span><span>STAL LINDENHORST - CSI** LINDENVELD</span></div>
    <div class="footer-web">
      <svg viewBox="0 0 20 20" fill="none" stroke="#fff" stroke-width="1.6"><circle cx="10" cy="10" r="8"/><ellipse cx="10" cy="10" rx="3.5" ry="8"/><path d="M2 10h16"/></svg>
      <span>WWW.STALLINDENHORST.NL</span>
    </div>
  </footer>
</main>
</body>
</html>
```